We are a doctors medical practice
I need the business card to be eye catching and memorable,
to reflect professionalism, yet also warmth and care

the numbers need to be easy to see, for the elderly

and the logo also in a location that is large enough to see and be eye catching

Back of card:
opening hours:
Mon- Fri 8.30am to 6pm
Sat 9am to 4pm

rows for appontments, date and time
Updates

HiĀ 

Modification to company name

BROOKVALE KINDRED HEALTH MEDICAL PRACTICE

Thanks
Marla

Reason: I am look for a unique design that also fulfils the design brief

I have attempted to post a .eps and .ai file of the logo

Target Market(s)

needs to appeal to the majority, mainly adults

Industry/Entity Type

Medical

Contact Information for Business Card

company name: Brookvale Kindred Health Medical Practice
Name: Dr Marla Tobrik-Vey
Qualifications: MBBS, BMedSc, FRACGP, DCH, FP Cert, Dip Skin
Address: Shop 3/41-43 Corrow St, Merrowdale 2173
Ph: 02 9184 3025
Fax: 02 9318 6042

Requirements
Nice to have
• I like balance
gold/ silver incorporated, as well as the other colours in the logo- but not limited to these colours
a "medical" feel
Should not have
• dark or strong colours

```html
<!DOCTYPE html>
<html lang="en">
<head>
<meta charset="utf-8">
<title>Brookvale Kindred Health Medical Practice – Business Card</title>
<link href="https://fonts.googleapis.com/css2?family=Montserrat:wght@800&family=Open+Sans:wght@400;600;700&family=Roboto+Condensed:wght@700&display=swap" rel="stylesheet">
<style>
  :root{
    --gold:#eec11a;
    --sky:#23a3dd;
    --brand-blue:#1a78c2;
    --ink:#4a4a4a;
    --white:#ffffff;
    --paper:#f3f3f3;
    --paper-shade:#dcdcdc;
    --rule:#555555;
    --backdrop:#e6e8ea;
  }
  *{box-sizing:border-box;margin:0;padding:0}
  html,body{width:1200px;height:900px;overflow:hidden}
  body{background:var(--backdrop);font-family:"Open Sans",Arial,sans-serif;position:relative}

  .card{position:absolute;left:280px;width:640px;height:388px;overflow:hidden;
        box-shadow:0 6px 18px rgba(0,0,0,.18);background:var(--white)}
  .card--back{top:36px}
  .card--front{top:474px}

  /* Back */
  .hours-band{height:92px;background:var(--gold);padding:20px 28px;display:flex;gap:14px;
              font-weight:600;color:var(--ink);font-size:21px;line-height:1.2}
  .hours-band .label{font-weight:700;letter-spacing:.5px;align-self:flex-end}
  .appointments{position:relative;height:296px;background:linear-gradient(180deg,var(--paper) 0%,var(--paper-shade) 100%);padding:16px 28px}
  .appointments .head{display:flex;justify-content:space-between;font-size:14px;font-weight:700;color:var(--ink);margin-bottom:6px}
  .rows{list-style:none;position:relative}
  .rows li{height:29px;border-bottom:2px dotted var(--rule)}
  .faint-ring{position:absolute;left:230px;top:-10px;width:260px;height:260px;border-radius:50%;
              border:10px solid rgba(35,163,221,.15);box-shadow:inset 0 0 0 14px rgba(124,194,66,.10)}

  /* Front */
  .front-gold{height:148px;background:var(--gold);padding:24px 30px 0 0;position:relative}
  .doctor{text-align:right;font-family:"Montserrat",Arial,sans-serif;font-weight:800;font-size:30px;color:var(--ink);letter-spacing:.5px}
  .quals{position:absolute;left:268px;top:72px;color:var(--white);font-weight:600;font-size:16px;line-height:1.3}
  .front-white{height:96px;display:flex;align-items:center;gap:14px;padding-left:26px;position:relative}
  .mark{width:72px;height:72px;border-radius:50%;border:5px solid var(--brand-blue);flex:none}
  .practice{font-family:"Roboto Condensed",Arial,sans-serif;font-weight:700;font-size:25px;color:var(--brand-blue);letter-spacing:.3px;white-space:nowrap}
  .front-blue{height:144px;background:var(--sky);padding:18px 40px;color:var(--white)}
  .contact{display:grid;grid-template-columns:110px 18px 1fr;row-gap:2px;font-size:21px;font-weight:600;line-height:1.4}
  .deco-ring{position:absolute;right:-60px;top:130px;width:220px;height:220px;border-radius:50%;
             background:radial-gradient(circle,rgba(255,255,255,.35) 0%,rgba(35,163,221,.25) 70%)}
</style>
</head>
<body>

<section class="card card--back" aria-label="Back of business card">
  <header class="hours-band">
    <span class="label">OPENING HOURS:</span>
    <span class="times">Mon– Fri 8.30am to 6pm<br>Sat 9am to 4pm</span>
  </header>
  <div class="appointments">
    <div class="faint-ring" role="img" aria-label="Faint practice emblem decoration"></div>
    <div class="head"><span>Appontments</span><span>Date &amp; Time</span></div>
    <ul class="rows"><li></li><li></li><li></li><li></li><li></li><li></li><li></li><li></li></ul>
  </div>
</section>

<section class="card card--front" aria-label="Front of business card">
  <div class="front-gold">
    <h1 class="doctor">Dr Marla Tobrik-Vey</h1>
    <p class="quals">MBBS, BMedSc, FRACGP,<br>DCH, FP Cert, Dip Skin</p>
  </div>
  <div class="front-white">
    <span class="mark"></span>
    <h2 class="practice">BROOKVALE KINDRED HEALTH MEDICAL PRACTICE</h2>
  </div>
  <div class="front-blue">
    <dl class="contact">
      <dt>Tel</dt><dd>:</dd><dd>02 9184 3025</dd>
      <dt>Fax</dt><dd>:</dd><dd>02 9318 6042</dd>
      <dt>Address</dt><dd>:</dd><dd>Shop 3/41-43 Corrow St, Merrowdale 2173</dd>
    </dl>
  </div>
  <div class="deco-ring" role="img" aria-label="Faint practice emblem decoration"></div>
</section>

</body>
</html>
```